Bright Harbor website redesign

We need a redesign for a website: mybrightharbor.example.

I already created a video going over what exactly is needed in the design.

See Video here: https://files.example.net/file/d/7xQpL2mR9vTz4KwB8nYcH3jDs6FgA1eU0/view?usp=sharing

Google Slide shown in Video: https://slides.example.net/presentation/d/9KP_Rtnwq3XbzmLeYc7VhJ2GoUd4Fs_PaiTe6q1kQ5Wr/edit?usp=sharing

Holidays in India so we did not get enough design entries or quality.

Target Market(s)

Dentistry

Industry/Entity Type

Dentistry

Number of Pages Required

1 page

Colors
0094D4
00A9DD
6FCCEA
C7EBF8
E9F6FB
00AB8E
00BBA5
67D7C9
C6EFE9
E9F9F6

Requirements
Must have
• See 13 min video link in description - shows what to do.

```html
<!DOCTYPE html>
<html lang="en">
<head>
<meta charset="utf-8">
<title>Bright Harbor – Meet Our Team</title>
<link href="https://fonts.googleapis.com/css2?family=Poppins:wght@400;600;700&family=Mulish:wght@400;600&display=swap" rel="stylesheet">
<style>
:root{
  --blue:#0094D4;
  --blue-light:#00A9DD;
  --green:#9DCB3A;
  --teal:#00AB8E;
  --ink:#3a3a3a;
  --text:#444;
  --grey-bg:#F5F5F5;
  --line:#e2e2e2;
}
*{margin:0;padding:0;box-sizing:border-box}
html,body{width:931px;height:1200px;overflow:hidden;background:#fff}
body{position:relative;font-family:"Mulish",sans-serif;color:var(--text)}
.abs{position:absolute}

/* header */
.site-header{position:absolute;left:0;top:0;width:931px;height:81px;background:#fff}
.brand{left:66px;top:26px;display:flex;align-items:center;gap:6px;font-family:"Mulish",sans-serif;font-weight:600;font-size:20px;color:var(--teal)}
.brand-dot{width:12px;height:12px;border-radius:50%;background:#d9262c}
.top-phone{left:500px;top:6px;display:flex;align-items:center;gap:5px;color:var(--blue);font-weight:600;font-size:13px;font-family:"Poppins",sans-serif}
.btn-top{top:0;height:27px;width:119px;color:#fff;font-family:"Poppins",sans-serif;font-weight:600;font-size:9.5px;display:flex;align-items:center;justify-content:center}
.btn-schedule{left:631px;background:var(--blue)}
.btn-emergency{left:752px;background:var(--green)}
.main-nav{left:233px;top:50px;display:flex;gap:0;font-size:11px;color:#555}
.main-nav span{margin-right:29px;position:relative}
.main-nav .caret::after{content:"";display:inline-block;margin-left:3px;border:3.5px solid transparent;border-top:4px solid #999;vertical-align:middle}
.nav-active{left:231px;top:80px;width:92px;height:1.5px;background:var(--teal)}

/* hero */
.hero{left:0;top:81px;width:931px;height:250px;background:linear-gradient(90deg,#8c8f93,#b9bcbf 45%,#9ea2a5)}
.hero-title{left:0;top:163px;width:878px;text-align:center;font-family:"Poppins",sans-serif;font-size:36px;color:#fff;font-weight:400}
.hero-title b{font-weight:700}
.crumbs{left:0;top:301px;width:931px;height:30px;background:rgba(225,225,225,.85);font-size:9.5px;color:#222;padding:10px 0 0 76px;font-family:"Poppins",sans-serif}

/* profile */
.portrait{left:76px;top:399px;width:261px;height:304px;border-radius:10px;background:linear-gradient(180deg,#efefef,#d9d6d8 55%,#3c4254)}
.doc-name{left:368px;top:394px;font-family:"Poppins",sans-serif;font-weight:700;font-size:23px;color:var(--ink)}
.doc-role{left:368px;top:418px;font-family:"Poppins",sans-serif;font-size:18px;color:var(--blue-light)}
.bio{left:368px;top:454px;width:490px;font-size:10.4px;line-height:18px;color:#333}
.bio p{margin-bottom:5px}
.bio p.tight{line-height:15px;margin:10px 0 13px}
.orgs{left:371px;top:683px;display:grid;grid-template-columns:212px 230px;row-gap:5px;font-size:10px;color:#2f4a4d;font-weight:600}
.orgs div{display:flex;align-items:center;gap:6px;height:16px}

/* info footer */
.info{left:0;top:815px;width:931px;height:294px;background:var(--grey-bg)}
.info h3{position:absolute;top:871px;font-family:"Poppins",sans-serif;font-size:18px;font-weight:400;color:#222}
.info-h b{font-weight:700}
.contact{left:110px;top:910px;font-size:10.3px;color:#333;line-height:16px}
.contact .row{display:flex;gap:9px;margin-bottom:13px}
.book{left:108px;top:1020px;width:167px;height:35px;background:var(--green);color:#fff;font-family:"Poppins",sans-serif;font-weight:600;font-size:10.5px;display:flex;align-items:center;justify-content:center}
.hours{left:367px;top:912px;font-size:10.3px;color:#333;display:grid;grid-template-columns:89px 80px;row-gap:9.3px}
.map{left:595px;top:908px;width:238px;height:142px;border:1px solid #e6c9cf;border-radius:3px;background:linear-gradient(135deg,#f1f1f1,#ececec 60%,#f6efdd)}

/* bottom bar */
.bottom{left:0;top:1109px;width:931px;height:91px;border-top:1px solid #dcdde3;background:var(--grey-bg)}
.foot-nav{left:112px;top:1130px;font-size:10px;color:#333;display:flex}
.foot-nav span{margin-right:26.5px}
.copy{left:112px;top:1158px;font-size:8.5px;color:#333}
.social{left:726px;top:1128px;display:flex;gap:4px}
.social i{width:19px;height:19px;border-radius:50%;background:var(--green);display:block}
.social i:first-child{background:#444}
</style>
</head>
<body>

<header class="site-header">
  <div class="abs brand"><span class="brand-dot"></span>Bright Harbor</div>
  <div class="abs top-phone">
    <svg width="17" height="17" viewBox="0 0 20 20"><circle cx="10" cy="10" r="10" fill="#0094D4"/><path d="M7 5.5l1.6 2.3-1 1.2c.7 1.4 1.6 2.3 3 3l1.2-1 2.3 1.6-1 1.9c-3.7-.4-6.6-3.3-7-7z" fill="#fff"/></svg>
    (555) 014-2287
  </div>
  <div class="abs btn-top btn-schedule">Schedule Online</div>
  <div class="abs btn-top btn-emergency">Emergency</div>
  <nav class="abs main-nav">
    <span class="caret">Meet Our Team</span><span class="caret">Services</span><span>Financing</span><span>Testimonials</span><span>New Patient Visit</span><span>Specials</span><span>Contact Us</span><span style="margin-right:0">Blog</span>
  </nav>
  <div class="abs nav-active"></div>
</header>

<section class="abs hero" role="img" aria-label="Dental team treating a patient in a clinic"></section>
<h1 class="abs hero-title">Meet <b>Our Team</b></h1>
<div class="abs crumbs">Home &gt;&gt; Meet Our Team</div>

<div class="abs portrait" role="img" aria-label="Portrait photo of the endodontist"></div>
<h2 class="abs doc-name">Dr. Anika Rao</h2>
<div class="abs doc-role">Endodontist</div>
<div class="abs bio">
  <p>Dr. Rao received her specialty training in Endodontics from Westbrook University. She graduated with a Master of Science in dentistry degree, in endodontics. She has practiced in Southern California for many years as a general dentist before specializing in endodontics and uses her experience to help her patients make the right decisions, regarding their treatment plans. She is gentle, compassionate and is committed to providing the optimum care for her patients.</p>
  <p style="margin-top:11px">Dr. Rao is a member of several professional and service organizations, including:</p>
  <p class="tight">Dr. Rao is an active member of the National Society of Endodontic Care and keeps herself updated with the latest methods and technologies in endodontics. In her free time, Dr. Rao enjoys cooking, travelling, and spending time with her family.</p>
  <p>Dr. Rao is a member of several professional and service organizations, including:</p>
</div>
<div class="abs orgs">
  <div><svg width="16" height="16" viewBox="0 0 16 16"><circle cx="8" cy="8" r="7.2" fill="none" stroke="#00BBA5" stroke-width="1.2"/><path d="M4.5 8.2l2.3 2.3 4.7-4.8" fill="none" stroke="#00BBA5" stroke-width="1.3"/></svg>National Dental Society (NDS)</div>
  <div><svg width="16" height="16" viewBox="0 0 16 16"><circle cx="8" cy="8" r="7.2" fill="none" stroke="#00BBA5" stroke-width="1.2"/><path d="M4.5 8.2l2.3 2.3 4.7-4.8" fill="none" stroke="#00BBA5" stroke-width="1.3"/></svg>Global Dental Forum (GDF)</div>
  <div><svg width="16" height="16" viewBox="0 0 16 16"><circle cx="8" cy="8" r="7.2" fill="none" stroke="#00BBA5" stroke-width="1.2"/><path d="M4.5 8.2l2.3 2.3 4.7-4.8" fill="none" stroke="#00BBA5" stroke-width="1.3"/></svg>State Dental Council (SDC)</div>
  <div><svg width="16" height="16" viewBox="0 0 16 16"><circle cx="8" cy="8" r="7.2" fill="none" stroke="#00BBA5" stroke-width="1.2"/><path d="M4.5 8.2l2.3 2.3 4.7-4.8" fill="none" stroke="#00BBA5" stroke-width="1.3"/></svg>Lakemont Dental Society (LDS)</div>
</div>

<section class="abs info"></section>
<h3 class="info-h" style="left:110px"><b>Bright</b> Harbor</h3>
<h3 class="info-h" style="left:367px"><b>Office</b> Hours</h3>
<h3 class="info-h" style="left:591px"><b>Our</b> Location</h3>

<div class="abs contact">
  <div class="row"><svg width="13" height="16" viewBox="0 0 12 16"><path d="M6 0a6 6 0 0 0-6 6c0 4.5 6 10 6 10s6-5.5 6-10a6 6 0 0 0-6-6z" fill="#3d4a55"/><circle cx="6" cy="6" r="2.2" fill="#F5F5F5"/></svg><span>48 Harbor View Ave., Suite A<br>Lakemont, CA 90000</span></div>
  <div class="row"><svg width="13" height="14" viewBox="0 0 20 20"><path d="M4 2l3.5 4-2 2.3c1.3 2.6 3.2 4.5 5.8 5.8l2.3-2 4 3.5-2.2 2.4C9 17.5 2.5 11 2 4.2z" fill="#3d4a55"/></svg><span>Call Us: (555) 014-2287</span></div>
  <div class="row"><svg width="14" height="12" viewBox="0 0 14 10" style="margin-top:3px"><rect width="14" height="10" fill="#3d4a55"/><path d="M0 0l7 5 7-5" fill="none" stroke="#F5F5F5" stroke-width="1.1"/></svg><span>hello@mybrightharbor.example</span></div>
</div>
<div class="abs book">BOOK APPOINTMENT</div>

<div class="abs hours">
  <span>Monday:</span><span>10AM–7PM</span>
  <span>Tuesday:</span><span>10AM–7PM</span>
  <span>Wednesday:</span><span>9AM–6PM</span>
  <span>Thursday:</span><span>9AM–6PM</span>
  <span>Friday:</span><span>9AM–5PM</span>
  <span>Saturday:</span><span>9AM–1PM</span>
</div>
<div class="abs map" role="img" aria-label="Street map showing the office location"></div>

<footer class="abs bottom"></footer>
<nav class="abs foot-nav"><span>About Us</span><span>Services</span><span>Financing</span><span>Testimonials</span><span>New Patient Visit</span><span>Specials</span><span>Contact Us</span><span>Blog</span></nav>
<div class="abs copy">2021 Bright Harbor &nbsp;| &nbsp; All Rights Reserved</div>
<div class="abs social" aria-label="Social links"><i></i><i></i><i></i><i></i><i></i></div>

</body>
</html>
```